Business Card Design

We are a manufacturing and distribution company with most of our customer base being supermarkets. We have established brand guidelines that are attached.

```html
<!DOCTYPE html>
<html lang="en">
<head>
<meta charset="utf-8">
<title>Corvella Business Card</title>
<link rel="stylesheet" href="https://fonts.googleapis.com/css2?family=Montserrat:wght@500;700;800&family=Arimo:wght@400&display=swap">
<style>
  :root {
    --backdrop: #d4d4d4;
    --card-white: #ffffff;
    --brand-blue: #0a6ab8;
    --brand-blue-light: #1586dd;
    --brand-blue-dark: #08589b;
    --brand-red: #e3232c;
    --ink: #1b1b1b;
    --rule: #d9d9d9;
  }
  * { box-sizing: border-box; margin: 0; padding: 0; }
  html, body {
    width: 1200px; height: 800px; overflow: hidden;
    background: var(--backdrop);
  }
  .stage {
    position: relative; width: 1200px; height: 800px;
    display: flex; align-items: center; justify-content: center; gap: 50px;
  }
  .card {
    position: relative; width: 525px; height: 300px;
    box-shadow: 0 10px 24px rgba(0,0,0,0.22);
    overflow: hidden;
  }

  /* Front */
  .card--front {
    background: var(--card-white);
    border-bottom: 3px solid var(--brand-blue);
    display: flex;
  }
  .front__brand {
    width: 50%;
    display: flex; align-items: center; justify-content: center; gap: 12px;
  }
  .brand-square {
    width: 26px; height: 26px; background: var(--brand-red);
  }
  .brand-name {
    font-family: "Montserrat", sans-serif; font-weight: 800;
    font-size: 34px; letter-spacing: 1px; color: var(--ink);
  }
  .front__divider {
    width: 1px; background: var(--rule); margin: 62px 0 40px;
  }
  .front__details {
    flex: 1; padding: 62px 0 0 24px;
    font-family: "Arimo", sans-serif; color: var(--ink);
  }
  .person-name {
    font-family: "Montserrat", sans-serif; font-weight: 800;
    font-size: 20px; letter-spacing: 0.5px; text-transform: uppercase;
  }
  .person-name__first { color: var(--brand-red); }
  .person-name__last { color: var(--brand-blue); }
  .person-role { font-size: 14px; margin-top: 2px; }
  .contact-list { list-style: none; margin-top: 16px; }
  .contact-list li {
    display: flex; align-items: center; gap: 7px;
    font-size: 14px; line-height: 22px;
  }
  .contact-icon { width: 13px; height: 13px; flex: none; }
  .web-highlight { color: var(--brand-blue); }
  .address { font-size: 14px; line-height: 19px; margin-top: 16px; }

  /* Back */
  .card--back {
    background: var(--brand-blue);
    border-bottom: 3px solid var(--brand-red);
  }
  .back__pattern {
    position: absolute; inset: 0;
    background: linear-gradient(200deg, var(--brand-blue-light) 0%, var(--brand-blue) 50%, var(--brand-blue-dark) 100%);
  }
  .back__brand {
    position: absolute; left: 0; right: 0; top: 50%;
    transform: translateY(-50%);
    display: flex; align-items: center; justify-content: center; gap: 12px;
  }
  .back__brand .brand-square { background: var(--brand-red); }
  .back__brand .brand-name { color: var(--card-white); }
</style>
</head>
<body>
<main class="stage">
  <section class="card card--front">
    <div class="front__brand">
      <span class="brand-square"></span>
      <span class="brand-name">CORVELLA</span>
    </div>
    <div class="front__divider"></div>
    <div class="front__details">
      <p class="person-name"><span class="person-name__first">Daniel</span> <span class="person-name__last">Hart</span></p>
      <p class="person-role">Managing Director</p>
      <ul class="contact-list">
        <li>
          <svg class="contact-icon" viewBox="0 0 16 16"><path fill="#e3232c" d="M3.6 1.2l2.3 2.6-1.4 2a8.5 8.5 0 0 0 5.7 5.7l2-1.4 2.6 2.3-1.6 2.3C7.4 14.5 1.5 8.6 1.3 2.8z"/></svg>
          044-555 010 234
        </li>
        <li>
          <svg class="contact-icon" viewBox="0 0 16 16"><rect x="1" y="3" width="14" height="10" fill="#e3232c"/><path d="M1 3l7 6 7-6" fill="none" stroke="#fff" stroke-width="1.4"/></svg>
          hello@corvella.com
        </li>
        <li>
          <svg class="contact-icon" viewBox="0 0 16 16"><circle cx="8" cy="8" r="7" fill="#e3232c"/><g fill="none" stroke="#fff" stroke-width="1"><ellipse cx="8" cy="8" rx="3" ry="6.5"/><path d="M1.5 8h13M2.5 5h11M2.5 11h11"/></g></svg>
          www.<span class="web-highlight">corvella</span>.com
        </li>
      </ul>
      <p class="address">88, Harbour Row, Unit 5<br>30917, Northland</p>
    </div>
  </section>

  <section class="card card--back">
    <div class="back__pattern" role="img" aria-label="Embossed repeating brand pattern in blue tones"></div>
    <div class="back__brand">
      <span class="brand-square"></span>
      <span class="brand-name">CORVELLA</span>
    </div>
  </section>
</main>
</body>
</html>
```